Create a banner for me that embodies my health and well being package.

I am an intuitive counselor with a busy practice helping clients to shift their blocks and move forward in their lives.
I have created a package called '9 paths home again'
I am wanting a banner to put on my website page, facebook page and to use as a letter head in mailouts.
My ideal clients are those who want to create change in their lives and who invest money in themselves and their personal and spiritual growth.
I am different to regular life coaches as my sessions have a spiritual twist to them creating much deeper change in my clients.
I would like the banner to be mainly font with the title of the progam: 9 Paths Home Again (no other wording) (something along the lines of the Blackjack font) and that ties in with the theme of my website. I'm not sure what else I want with it and am looking for ideas.
Website:
www.lumorawellspring.com.au
I also have a current facebook page for the business:
https://www.facebook.com/Lumora-Wellspring-Studio-502718364091557/
(Note: I am about to drop my logo and business name and move to using my own name - the rest of the website will remain the same).
I have attached a doc with the draft of what wording will be on the website page any advertising will link to, to give you an idea of what the program is about.

Target Market(s)

People who invest money on themselves who are looking to improve their emotional well being and creating change in their life. Majority are middle aged women (also younger females and some men)

Industry/Entity Type

Health And Wellness

Font styles to use
Other font styles liked:
• I like Blackjack and Amienne. Along those lines.

Requirements
Must have
• Attractive, modern and GREAT font.
Nice to have
• Surprise me with something amazing!
• I love the colours in the 2 images I have up loaded as they represent the heart chakra colours. They could be a feature on the banner or blurred into the background.
Should not have
• Even though my work is quite spiritual I don't want it to look woo woo (meaning airy fairy spiritual stuff!)

```html
<!DOCTYPE html>
<html lang="en">
<head>
<meta charset="utf-8">
<title>9 Paths Home Again – Banner</title>
<link rel="stylesheet" href="https://fonts.googleapis.com/css2?family=Yellowtail&family=Dancing+Script:wght@700&family=Oswald:wght@300;400&display=block">
<style>
  :root {
    --page-bg: #e9e7e8;
    --violet: #5a5ab8;
    --violet-light: #8a8ad8;
    --violet-deep: #4646a0;
    --white: #ffffff;
    --pill-text: #3a3a3a;
    --ring-green: #b6e3a8;
  }
  * { margin: 0; padding: 0; box-sizing: border-box; }
  html, body { width: 1200px; height: 1200px; overflow: hidden; background: var(--page-bg); }
  .canvas { position: relative; width: 1200px; height: 1200px; }
  .banner {
    position: absolute; left: 102px; top: 392px; width: 997px; height: 416px;
    overflow: hidden;
    background:
      radial-gradient(ellipse at 30% 30%, var(--violet-light) 0%, transparent 60%),
      radial-gradient(ellipse at 95% 50%, var(--violet-light) 0%, transparent 40%),
      linear-gradient(180deg, var(--violet) 0%, var(--violet-deep) 100%);
  }
  .artwork { position: absolute; inset: 0; width: 997px; height: 416px; }
  .title {
    position: absolute; left: 84px; top: 22px;
    font-family: "Yellowtail", "Dancing Script", cursive;
    font-weight: 400;
    color: var(--white);
    text-shadow: 0 3px 6px rgba(30,30,90,0.45);
    line-height: 1;
    white-space: nowrap;
  }
  .title-line-one { display: block; font-size: 120px; }
  .title-line-two { display: block; font-size: 86px; margin-left: -10px; margin-top: -10px; }
  .tagline-pill {
    position: absolute; left: 43px; top: 262px; width: 500px; height: 56px;
    border-radius: 28px;
    background: linear-gradient(180deg, #ffffff 0%, #e4e4ea 100%);
    box-shadow: 0 3px 8px rgba(20,20,70,0.35);
    display: flex; align-items: center; padding-left: 26px;
    font-family: "Oswald", sans-serif; font-weight: 400; font-size: 25px;
    color: var(--pill-text); letter-spacing: -0.2px;
  }
  .web-address {
    position: absolute; left: 74px; top: 342px;
    font-family: "Oswald", sans-serif; font-weight: 300; font-size: 27px;
    color: var(--white); letter-spacing: 0.2px;
  }
</style>
</head>
<body>
<div class="canvas">
  <section class="banner">
    <svg class="artwork" viewBox="0 0 997 416" xmlns="http://www.w3.org/2000/svg">
      <defs>
        <radialGradient id="lotusPhoto" cx="45%" cy="65%" r="70%">
          <stop offset="0%" stop-color="#f08cc0"/>
          <stop offset="30%" stop-color="#d4488c"/>
          <stop offset="55%" stop-color="#7db84a"/>
          <stop offset="100%" stop-color="#3f7a2c"/>
        </radialGradient>
        <radialGradient id="statuePhoto" cx="50%" cy="50%" r="60%">
          <stop offset="0%" stop-color="#8b8877"/>
          <stop offset="100%" stop-color="#4e4c42"/>
        </radialGradient>
        <linearGradient id="bowlPhoto" x1="0" y1="0" x2="0" y2="1">
          <stop offset="0%" stop-color="#8a7f86"/>
          <stop offset="55%" stop-color="#8e4a6e"/>
          <stop offset="100%" stop-color="#d9b49a"/>
        </linearGradient>
      </defs>

      <path class="sweep-white" d="M 554 24 C 610 10 650 0 700 0 L 720 0 C 660 60 690 150 620 250 C 580 310 560 370 590 416 L 560 416 C 520 360 540 290 580 230 C 640 140 640 60 554 24 Z" fill="#ffffff" opacity="0.95"/>

      <path class="feature-rim" d="M 600 0 L 830 0 C 900 20 960 80 960 180 C 960 260 940 330 900 416 L 585 416 C 560 360 580 300 625 230 C 680 140 650 60 600 0 Z" fill="var(--ring-green)"/>
      <path class="feature-rim-inner" d="M 612 0 L 820 0 C 890 22 948 84 948 180 C 948 258 930 330 890 416 L 598 416 C 575 360 592 302 636 234 C 692 144 664 62 612 0 Z" fill="#ffffff"/>

      <path role="img" aria-label="Photograph of a pink lotus flower opening above a dark green leaf against a blurred green garden"
            d="M 622 0 L 812 0 C 880 24 938 88 938 180 C 938 256 918 330 878 416 L 610 416 C 588 360 604 304 646 238 C 704 146 674 62 622 0 Z"
            fill="url(#lotusPhoto)"/>

      <circle cx="868" cy="116" r="96" fill="var(--ring-green)"/>
      <circle cx="868" cy="116" r="90" fill="#ffffff"/>
      <circle role="img" aria-label="Photograph of a bronze meditation statue" cx="868" cy="116" r="84" fill="url(#statuePhoto)"/>

      <circle cx="915" cy="298" r="70" fill="var(--ring-green)"/>
      <circle cx="915" cy="298" r="65" fill="#ffffff"/>
      <circle role="img" aria-label="Photograph of a wooden bowl of dried rose petals" cx="915" cy="298" r="60" fill="url(#bowlPhoto)"/>
    </svg>

    <h1 class="title">
      <span class="title-line-one">9 paths</span>
      <span class="title-line-two">home again</span>
    </h1>

    <p class="tagline-pill">Seeing the world from the eyes of your heart</p>

    <p class="web-address">www.lumorawellspring.com.au</p>
  </section>
</div>
</body>
</html>
```